Website Design for The Elder Nook

Please design and code a new website.
Here are the sites I like best:
http://www.voyaglint.com/alternate/
http://www.wheelgiftbay.org
Please make it similar but look at the competitor site (below) for images and wording. This is NOT a car donation site. It's a senior lead placement site like https://www.kinhavenfinder.com. I just like this sites above as a lead generation sites.
Competitor site:
https://www.kinhavenfinder.com (use ideas / verbiage from this site)
Updates
Competitor site:
Coding
Coded - Design and coding required
Number of Pages Required
1 page
Look and feel
Each slider illustrates characteristics of the customer's brand and the style your logo design should communicate.

```html
<!DOCTYPE html>
<html lang="en">
<head>
<meta charset="utf-8">
<title>The Elder Nook — Senior Living Advisors</title>
<link href="https://fonts.googleapis.com/css2?family=Frank+Ruhl+Libre:wght@400;500&family=Jost:wght@300;400;500&display=swap" rel="stylesheet">
<style>
:root{
  --blue:#0c5bb0;
  --blue-dark:#0a4f9c;
  --blue-light:#2a72c2;
  --green:#8cc63f;
  --text:#333;
  --muted:#777;
  --line:#e2e2e2;
  --serif:"Frank Ruhl Libre",Georgia,serif;
  --sans:"Jost",Arial,sans-serif;
}
*{box-sizing:border-box;margin:0;padding:0}
html,body{width:1200px;height:2984px;overflow:hidden}
body{font-family:var(--sans);color:var(--text);background:#fff;position:relative}
.wrap{width:918px;margin:0 auto;position:relative}
a{color:inherit;text-decoration:none}

/* header */
.site-header{height:91px}
.site-header .wrap{height:91px;display:flex;align-items:center;justify-content:space-between}
.brand{display:flex;align-items:center;gap:10px;font-family:var(--sans);font-size:24px;color:var(--blue);font-weight:400}
.brand-dot{width:26px;height:26px;border-radius:50%;background:var(--green)}
.header-right{display:flex;align-items:center;gap:36px}
.call{display:flex;align-items:center;gap:10px}
.call small{display:block;font-family:var(--serif);font-size:11px;color:#555}
.call strong{display:block;font-weight:400;font-size:24px;color:#333;line-height:1}
.lang{width:102px;height:34px;background:var(--green);display:flex;align-items:center;justify-content:center;gap:8px;color:#fff;font-size:12px}
.flag{width:34px;height:18px;background:linear-gradient(#c9303a 0 50%,#2d3f7a 50%)}

/* nav */
.main-nav{background:var(--blue);height:42px}
.main-nav ul{list-style:none;display:flex;height:42px}
.main-nav li{font-family:var(--serif);font-size:13px;color:#fff;padding:0 11px;display:flex;align-items:center;border-right:1px solid rgba(255,255,255,.2)}
.main-nav li.active{background:var(--blue-light);border-bottom:3px solid var(--green)}

/* hero */
.hero{height:517px;background:linear-gradient(90deg,#e9eaec,#dcdee1);position:relative}
.hero-photo{position:absolute;left:520px;top:0;right:0;bottom:0;background:linear-gradient(100deg,#d8d6d2,#c9b8a4 40%,#8ca9cf 70%,#d9cbb5)}
.hero .wrap{padding-top:78px}
.hero h1{font-family:var(--serif);font-weight:400;font-size:34px;line-height:42px;color:#333}
.hero h1 em{color:var(--blue)}
.hero .sub{font-size:20px;font-weight:300;margin:6px 0 14px -2px}
.field{width:372px;height:46px;border:1px solid #ccc;background:#fff;font-size:14px;padding:0 20px;display:flex;align-items:center;color:#444}
.btn{background:var(--green);color:#fff;font-family:var(--serif);display:flex;align-items:center;justify-content:center}
.hero .btn{width:372px;height:48px;font-size:17px;margin-top:10px}
.need{font-size:20px;margin:28px 0 14px -2px}
.badge{width:156px;height:58px;border-radius:6px;background:var(--blue)}

/* support */
.support{height:545px;text-align:center;padding-top:76px}
.sec-title{font-family:var(--serif);font-weight:400;font-size:30px;color:var(--green)}
.sec-title span{color:var(--blue)}
.lead{font-size:14px;line-height:24px;color:#444;margin-top:12px}
.cards{display:flex;gap:15px;margin-top:30px}
.card{width:172px;height:181px;border:1px solid var(--line);box-shadow:0 2px 4px rgba(0,0,0,.06);padding-top:24px;font-size:18px;font-weight:300;line-height:21px}
.card svg{display:block;margin:0 auto 8px}
.no-cost{display:flex;align-items:center;justify-content:space-between;margin-top:50px;text-align:left}
.no-cost h3{font-family:var(--serif);font-weight:400;font-size:25px;color:var(--green)}
.no-cost h3 span{color:var(--blue)}
.no-cost p{font-size:17px;font-weight:300;line-height:24px}
.no-cost .tel{font-size:21px;color:var(--blue)}

/* advisor */
.advisor{height:480px;background:var(--blue-dark);position:relative;color:#fff;text-align:center}
.advisor-bg{position:absolute;inset:0;background:repeating-linear-gradient(90deg,#1b62b3 0 150px,#15589f 150px 180px,#2268b5 180px 360px)}
.advisor .wrap{padding-top:78px}
.advisor h2{font-family:var(--serif);font-weight:400;font-size:30px}
.advisor .lead{color:#fff;margin-top:8px}
.perks{display:flex;justify-content:center;gap:165px;margin-top:18px}
.perk{width:96px;font-size:16px;font-weight:300;line-height:20px;display:flex;flex-direction:column;align-items:center}
.perk .ring{width:96px;height:96px;border:1.5px solid #fff;border-radius:50%;display:flex;align-items:center;justify-content:center}
.perk span{width:190px;margin-top:12px}
.advisor-search{width:604px;height:46px;margin:30px auto 0;background:#fff;display:flex;align-items:center;justify-content:space-between;padding:0 4px 0 20px;color:#444;font-size:14px}
.advisor-search .btn{width:222px;height:38px;font-size:16px}

/* testimonials */
.reviews{height:483px;text-align:center;padding-top:78px}
.quotes{display:flex;gap:32px;margin-top:22px;text-align:left}
.quote{width:285px}
.quote p{border:1px solid var(--line);height:147px;padding:18px 18px;font-size:13px;line-height:22px;color:var(--muted);letter-spacing:.3px}
.who{display:flex;align-items:center;gap:20px;margin:-20px 0 0 10px}
.avatar{width:70px;height:70px;border-radius:50%;border:3px solid var(--blue);background:linear-gradient(#e0c8ad,#b89576)}
.who b{font-family:var(--serif);font-weight:400;font-size:15px;margin-top:20px}
.reviews .btn{width:207px;height:38px;margin:26px auto 0;font-size:16px}

/* veterans */
.veterans{height:292px;position:relative;color:#fff;text-align:center}
.veterans-bg{position:absolute;inset:0;background:linear-gradient(160deg,#1a2238,#2a2f3e 45%,#4a4440 70%,#1c1e24)}
.veterans .wrap{padding-top:70px}
.veterans h2{font-family:var(--serif);font-weight:400;font-size:26px}
.veterans p{font-size:14px;line-height:24px;margin-top:6px}
.veterans .btn{width:130px;height:38px;margin:18px auto 0;font-size:16px}

/* states */
.states{height:365px;text-align:center;padding-top:78px}
.state-cols{display:flex;margin:24px 0 0 17px;text-align:left}
.state-cols ul{list-style:none;font-size:13px;line-height:22px;color:#333}
.state-cols li::before{content:"› "}

/* footer */
.site-footer{height:169px;background:var(--blue);color:#fff}
.foot-nav{display:flex;justify-content:center;gap:33px;font-family:var(--serif);font-size:12px;padding-top:50px;height:94px;border-bottom:1px solid rgba(255,255,255,.3)}
.foot-bottom{display:flex;justify-content:space-between;align-items:center;height:56px;font-size:14px}
.social{display:flex;gap:5px}
.social i{width:26px;height:26px;border-radius:50%;border:1px solid #fff;background:var(--blue-light)}
</style>
</head>
<body>

<header class="site-header">
  <div class="wrap">
    <div class="brand"><span class="brand-dot"></span>The Elder Nook</div>
    <div class="header-right">
      <div class="call">
        <svg width="36" height="36" viewBox="0 0 36 36" fill="none" stroke="#0c5bb0" stroke-width="2"><path d="M10 4l5 7-3 3c2 4 5 7 9 9l3-3 7 5-3 5c-11 0-24-13-24-24z"/><path d="M21 4a11 11 0 0 1 11 11M21 9a6 6 0 0 1 6 6"/></svg>
        <div><small>Talk to a local advisor for FREE</small><strong>(123) 456-7890</strong></div>
      </div>
      <div class="lang">En <span class="flag" role="img" aria-label="Country flag"></span>⌄</div>
    </div>
  </div>
</header>

<nav class="main-nav">
  <div class="wrap">
    <ul>
      <li class="active">ASSISTED LIVING</li>
      <li>MEMORY CARE</li>
      <li>NURSING HOMES</li>
      <li>MORE LIVING OPTIONS ⌄</li>
      <li>PLANNING &amp; ADVICE</li>
      <li style="border-right:0">HOW OUR SERVICE WORKS</li>
    </ul>
  </div>
</nav>

<section class="hero">
  <div class="hero-photo" role="img" aria-label="Photo of an advisor reviewing paperwork with a senior couple"></div>
  <div class="wrap">
    <h1>You know your family.<br>We know <em>Senior Living.</em></h1>
    <p class="sub">Find Senior Living Near You.</p>
    <div class="field">Enter city or postal code</div>
    <div class="btn">Start Your Search</div>
    <p class="need">Need help? Call (123) 456-7890</p>
    <div class="badge" role="img" aria-label="Accreditation badge"></div>
  </div>
</section>

<section class="support">
  <div class="wrap">
    <h2 class="sec-title">The Support You Need To <span>Make The Right Choice</span></h2>
    <p class="lead">Lorem ipsum dolor sit amet, consectetuer adipiscing elit, sed diam nonummy nibh euismod tincidunt ut laoreet dolore magna<br>aliquam erat volutpat. Ut wisi enim ad minim veniam, quis nostrud exerci tation ullamcorper suscipit.</p>
    <div class="cards">
      <div class="card"><svg width="50" height="56" viewBox="0 0 50 56" fill="none" stroke="#8cc63f" stroke-width="2"><circle cx="25" cy="14" r="9"/><path d="M8 55V38c0-6 6-10 17-10s17 4 17 10v17M19 28l6 14 6-14M25 42v13"/></svg>Dedicated local<br>advisor</div>
      <div class="card"><svg width="52" height="56" viewBox="0 0 52 56" fill="none" stroke="#8cc63f" stroke-width="2"><path d="M3 26L26 4l23 22M9 21v34h34V21M21 55V38h10v17M22 24h8v8h-8z"/></svg>Hand-picked list of<br>communities to<br>match your needs</div>
      <div class="card"><svg width="50" height="56" viewBox="0 0 50 56" fill="none" stroke="#8cc63f" stroke-width="2"><circle cx="27" cy="20" r="11"/><path d="M27 13v14M23 17h6a3 3 0 0 1 0 6h-4a3 3 0 0 0 0 6M27 2v4M4 44l10-6h12l6 4h10l-14 8H14"/></svg>Full details and<br>pricing</div>
      <div class="card"><svg width="54" height="56" viewBox="0 0 54 56" fill="none" stroke="#8cc63f" stroke-width="2"><rect x="3" y="8" width="48" height="46"/><path d="M3 18h48M13 3v10M41 3v10M12 26h30v20H12zM12 33h30M12 40h30M20 26v20M28 26v20M35 26v20"/></svg>Help scheduling<br>tours</div>
      <div class="card"><svg width="66" height="56" viewBox="0 0 66 56" fill="none" stroke="#8cc63f" stroke-width="2"><path d="M14 10h32v30H14zM46 20h10l8 10v10H46M2 18h10M5 26h9M8 34h6"/><circle cx="22" cy="44" r="5"/><circle cx="54" cy="44" r="5"/></svg>Move in<br>support</div>
    </div>
    <div class="no-cost">
      <h3>There's <span>No Cost To You.</span></h3>
      <p>We work with over 20,000 senior living communities.<br>Our community partners pay us for placement services.</p>
      <a class="tel">Call (123) 456-7890</a>
    </div>
  </div>
</section>

<section class="advisor">
  <div class="advisor-bg" role="img" aria-label="Blue-tinted row of portrait photos of local advisors"></div>
  <div class="wrap">
    <h2>Your local advisor informs. You decide.</h2>
    <p class="lead">Lorem ipsum dolor sit amet, consectetuer adipiscing elit, sed diam nonummy nibh euismod tincidunt ut laoreet.</p>
    <div class="perks">
      <div class="perk"><div class="ring"><svg width="34" height="60" viewBox="0 0 34 60" fill="none" stroke="#fff" stroke-width="2"><circle cx="17" cy="14" r="12"/><path d="M17 26v32"/></svg></div><span>Insider's tips for the area<br>near you</span></div>
      <div class="perk"><div class="ring"><svg width="54" height="48" viewBox="0 0 54 48" fill="none" stroke="#fff" stroke-width="2.5"><path d="M27 46L6 25A12 12 0 0 1 27 8a12 12 0 0 1 21 17z"/></svg></div><span>Advice tailored to your<br>unique situation</span></div>
      <div class="perk"><div class="ring"><svg width="52" height="46" viewBox="0 0 52 46" fill="none" stroke="#fff" stroke-width="2"><circle cx="6" cy="6" r="4"/><circle cx="6" cy="23" r="4"/><circle cx="6" cy="40" r="4"/><path d="M16 6h34M16 23h34M16 40h34"/></svg></div><span>Time saving know-how and<br>resources</span></div>
    </div>
    <div class="advisor-search">Enter city or postal code<div class="btn">Find an advisor near you</div></div>
  </div>
</section>

<section class="reviews">
  <div class="wrap">
    <h2 class="sec-title">93% Of Our Customers <span>Recommend Our Service</span></h2>
    <div class="quotes">
      <div class="quote"><p>Lorem ipsum dolor sit amet, consectetuer adipiscing elit, sed diam nonummy nibh euismod tincidunt ut laoreet dolore magna aliquam erat volutpat. Ut wisi enim ad minim veniam, quis nostrud.</p><div class="who"><div class="avatar" role="img" aria-label="Customer portrait"></div><b>Dana Reyes</b></div></div>
      <div class="quote"><p>Lorem ipsum dolor sit amet, consectetuer adipiscing elit, sed diam nonummy nibh euismod tincidunt ut laoreet dolore magna aliquam erat volutpat. Ut wisi enim ad minim veniam, quis nostrud.</p><div class="who"><div class="avatar" role="img" aria-label="Customer portrait"></div><b>Owen Marsh</b></div></div>
      <div class="quote"><p>Lorem ipsum dolor sit amet, consectetuer adipiscing elit, sed diam nonummy nibh euismod tincidunt ut laoreet dolore magna aliquam erat volutpat. Ut wisi enim ad minim veniam, quis nostrud.</p><div class="who"><div class="avatar" role="img" aria-label="Customer portrait"></div><b>Lena Hart</b></div></div>
    </div>
    <div class="btn">See More Testimonials</div>
  </div>
</section>

<section class="veterans">
  <div class="veterans-bg" role="img" aria-label="Dark photo of a waving national flag"></div>
  <div class="wrap">
    <h2>Access Up To $2,000 Per Month In Veteran's Aid</h2>
    <p>We work with Veterans every day. Most veteran families do not know of a key benefit available to them and their families.<br>It's called the Veteran's Aid and Attendance benefit. This benefit can help pay for senior living and home care.</p>
    <div class="btn">Learn More</div>
  </div>
</section>

<section class="states">
  <div class="wrap">
    <h2 class="sec-title">Senior Assisted <span>Living by State</span></h2>
    <div class="state-cols">
      <ul style="width:143px"><li>Alabama</li><li>Arizona</li><li>Arkansas</li><li>California</li><li>Colorado</li><li>Connecticut</li><li>Delaware</li></ul>
      <ul style="width:185px"><li>District of Columbia</li><li>Florida</li><li>Georgia</li><li>Hawaii</li><li>Idaho</li><li>Illinois</li><li>Indiana</li></ul>
      <ul style="width:158px"><li>Iowa</li><li>Kansas</li><li>Kentucky</li><li>Louisiana</li><li>Maine</li><li>Maryland</li><li>Massachusetts</li></ul>
      <ul style="width:136px"><li>Michigan</li><li>Minnesota</li><li>Mississippi</li><li>Missouri</li><li>Montana</li><li>Nebraska</li><li>Nevada</li></ul>
      <ul style="width:169px"><li>New Hampshire</li><li>New Jersey</li><li>New Mexico</li><li>New York</li><li>North Carolina</li><li>North Dakota</li><li>Ohio</li></ul>
      <ul><li>Oklahoma</li><li>Oregon</li><li>Pennsylvania</li><li>Rhode Island</li><li>South Carolina</li><li>South Dakota</li><li>Tennessee</li></ul>
    </div>
  </div>
</section>

<footer class="site-footer">
  <div class="wrap">
    <div class="foot-nav"><span>ASSISTED LIVING</span><span>MEMORY CARE</span><span>NURSING HOMES</span><span>MORE LIVING OPTIONS ⌄</span><span>PLANNING &amp; ADVICE</span><span>HOW OUR SERVICE WORKS</span></div>
    <div class="foot-bottom"><span>Copyright 2019 The Elder Nook. All Rights Reserved.</span><div class="social"><i></i><i></i><i></i><i></i></div></div>
  </div>
</footer>

</body>
</html>
```